Jewellery Store Web design

We are looking at a redesign of an exclusive jewellery store. The idea of what we want is to display the type of jewellery we sell. Our main product range is white diamonds. We do not want people to buy online. This site will not display any prices but only display photos and the information about the store.
The client believes in the saying “A picture makes a thousand words” so this site needs to be more pictures – less words.
The website that the client loves is:
www.plovenjewels.com
The existing site can be found at:
http://www.marlowvaultstore.com.au/
The site cannot be written in flash as the site must be viewable on Zentab/Kovafon devices and will be implemented with our already designed CMS.
This project is only for the PSD file. We will code up the final submission ourselves.
Updates
Reason: We have some great designs and we have decided to gurrantee the project and for those who want a payment gurrantee to enter.
Target Market(s)
Young Couples, 30+
Industry/Entity Type
Store
Look and feel
Each slider illustrates characteristics of the customer's brand and the style your logo design should communicate.

```html
<!DOCTYPE html>
<html lang="en">
<head>
<meta charset="utf-8">
<title>Marlow Vault — Fine Jewellery</title>
<link href="https://fonts.googleapis.com/css2?family=PT+Sans:wght@400;700&family=PT+Sans+Narrow:wght@400;700&display=swap" rel="stylesheet">
<style>
  :root {
    --page-bg: #1c1c1c;
    --footer-bg: #000000;
    --stage-bg: #5c5c5c;
    --accent: #e2612a;
    --accent-dark: #c94b18;
    --text: #2b2b2b;
    --muted-line: #9a9a9a;
    --nav-top: #f7f7f7;
    --nav-bottom: #d6d6d6;
    --white: #ffffff;
  }
  * { box-sizing: border-box; margin: 0; padding: 0; }
  html, body { width: 1200px; height: 744px; overflow: hidden; }
  body {
    background: var(--page-bg);
    font-family: "PT Sans", Arial, sans-serif;
    position: relative;
  }
  .site { position: absolute; left: 153px; top: 0; width: 894px; height: 667px; background: var(--stage-bg); }
  .hero {
    position: absolute; left: 0; top: 0; width: 894px; height: 547px;
    background:
      radial-gradient(ellipse 260px 130px at 52% 52%, rgba(196,160,60,0.85), rgba(196,160,60,0) 100%),
      radial-gradient(ellipse 520px 340px at 55% 50%, #eeeeee 0%, #cfcfcf 60%, #8a8a8a 100%);
  }
  .brand {
    position: absolute; left: 0; width: 894px; top: 26px; text-align: center;
    font-family: "PT Sans Narrow", Arial, sans-serif; font-weight: 700;
    color: var(--white); font-size: 44px; letter-spacing: 3px; line-height: 1;
    text-transform: uppercase; white-space: nowrap;
  }
  .search {
    position: absolute; left: 668px; top: 47px; width: 201px; height: 25px;
    border-radius: 12px; background: linear-gradient(#ffffff, #dcdcdc);
    box-shadow: 0 1px 3px rgba(0,0,0,0.35);
    font-size: 12px; color: #444; padding: 6px 11px;
  }
  .search svg { position: absolute; right: 14px; top: 4px; }
  .main-nav {
    position: absolute; left: 24px; top: 107px; width: 845px; height: 28px;
    border-radius: 8px; background: linear-gradient(var(--nav-top), var(--nav-bottom));
    box-shadow: 0 1px 3px rgba(0,0,0,0.3); display: flex; overflow: hidden;
  }
  .main-nav a {
    display: flex; align-items: center; justify-content: center;
    font-size: 12.5px; color: #1e1e1e; text-decoration: none; white-space: nowrap;
    border-right: 1px solid #a9a9a9; height: 100%;
  }
  .main-nav a:last-child { border-right: 0; }
  .features {
    position: absolute; left: 26px; top: 460px; width: 846px; height: 190px;
    border-radius: 9px; background: rgba(226,226,226,0.82);
  }
  .feature { position: absolute; left: 0; top: 0; width: 846px; height: 190px; }
  .feature-title {
    position: absolute; font-family: "PT Sans Narrow", Arial, sans-serif;
    color: var(--accent); font-size: 21px; font-weight: 400; line-height: 1.2;
    white-space: nowrap;
  }
  .rule { position: absolute; height: 0; border-top: 1px dashed var(--muted-line); }
  .divider { position: absolute; top: 10px; height: 178px; border-left: 1px dotted #6f6f6f; }
  .slider-arrows { position: absolute; left: 225px; top: 16px; display: flex; gap: 5px; }
  .arrow { width: 17px; height: 17px; border-radius: 50%; background: var(--accent); display: flex; align-items: center; justify-content: center; }
  .thumb { position: absolute; top: 77px; height: 67px; border: 1px solid #fff; }
  .feature-image { position: absolute; top: 66px; width: 95px; height: 91px; border: 1px solid #8c8c8c; }
  .feature-text {
    position: absolute; top: 64px; width: 142px; font-size: 11px; line-height: 16.5px;
    color: var(--text); text-align: justify;
  }
  .read-more {
    position: absolute; top: 157px; width: 77px; height: 20px; border-radius: 10px;
    background: linear-gradient(#ef7a43, var(--accent-dark)); color: #fff; white-space: nowrap;
    font-size: 11px; display: flex; align-items: center; justify-content: center; text-decoration: none;
  }
  .site-footer { position: absolute; left: 0; top: 667px; width: 1200px; height: 77px; background: var(--footer-bg); }
  .footer-nav { position: absolute; left: 187px; top: 34px; font-size: 11.5px; color: #fff; white-space: nowrap; }
  .footer-nav a { color: #fff; text-decoration: none; }
  .footer-nav span { margin: 0 7px; }
  .copyright { position: absolute; left: 834px; top: 34px; font-size: 11.5px; color: #fff; white-space: nowrap; }
</style>
</head>
<body>
  <div class="site">
    <div class="hero" role="img" aria-label="Close-up of a gold band set with princess-cut diamonds in a white ring box"></div>

    <div class="brand">Marlow Vault</div>

    <div class="search">Search
      <svg width="14" height="14" viewBox="0 0 14 14"><circle cx="5.5" cy="5.5" r="4" fill="none" stroke="#777" stroke-width="1.5"/><line x1="8.5" y1="8.5" x2="13" y2="13" stroke="#777" stroke-width="2"/></svg>
    </div>

    <nav class="main-nav">
      <a href="#" style="width:145px">Home</a>
      <a href="#" style="width:136px">About Us</a>
      <a href="#" style="width:147px">Collection</a>
      <a href="#" style="width:140px">Diamonds</a>
      <a href="#" style="width:134px">Friends</a>
      <a href="#" style="width:143px">Contact Us</a>
    </nav>

    <section class="features">
      <div class="feature collection">
        <h2 class="feature-title" style="left:18px;top:15px">Collection</h2>
        <div class="slider-arrows">
          <span class="arrow"><svg width="7" height="8"><polygon points="6,0 0,4 6,8" fill="#fff"/></svg></span>
          <span class="arrow"><svg width="7" height="8"><polygon points="1,0 7,4 1,8" fill="#fff"/></svg></span>
        </div>
        <div class="rule" style="left:21px;top:48px;width:233px"></div>
        <div class="thumb" style="left:21px;width:71px;background:linear-gradient(135deg,#f4f4f4,#d9c27a)" role="img" aria-label="Diamond solitaire ring on gold band"></div>
        <div class="thumb" style="left:100px;width:71px;background:linear-gradient(135deg,#a87a6a,#f0e6e0)" role="img" aria-label="Diamond ring in a pink box"></div>
        <div class="thumb" style="left:185px;width:69px;background:linear-gradient(135deg,#ffffff,#c9b46a)" role="img" aria-label="Gold diamond band on white"></div>
      </div>

      <div class="divider" style="left:280px"></div>

      <div class="feature diamonds">
        <h2 class="feature-title" style="left:301px;top:10px">Diamonds</h2>
        <div class="rule" style="left:305px;top:48px;width:233px"></div>
        <div class="feature-image" style="left:305px;background:linear-gradient(135deg,#f2f2f2,#a9a9a9)" role="img" aria-label="Cluster of diamond rings"></div>
        <p class="feature-text" style="left:408px">The popular and overly simple four - clarity, colour and carat weight - are commonly used to determine the value of a diamond.</p>
        <a class="read-more" href="#" style="left:412px">Read More&gt;&gt;</a>
      </div>

      <div class="divider" style="left:562px"></div>

      <div class="feature about">
        <h2 class="feature-title" style="left:582px;top:12px">About Us</h2>
        <div class="rule" style="left:590px;top:48px;width:233px"></div>
        <div class="feature-image" style="left:587px;background:linear-gradient(135deg,#f5f1ec,#c9b7c6)" role="img" aria-label="Pearl necklace with pink stone clasps"></div>
        <p class="feature-text" style="left:689px">The popular and overly simple four - clarity, colour and carat weight - are commonly used to determine the value of a diamond.</p>
        <a class="read-more" href="#" style="left:690px">Read More&gt;&gt;</a>
      </div>
    </section>
  </div>

  <footer class="site-footer">
    <nav class="footer-nav">
      <a href="#">Home</a><span>|</span><a href="#">About Us</a><span>|</span><a href="#">Collection</a><span>|</span><a href="#">Diamonds</a><span>|</span><a href="#">Friends</a><span>|</span><a href="#">Contact</a>
    </nav>
    <p class="copyright">Copyrightds @ 2012 All Rights Reserved</p>
  </footer>
</body>
</html>
```